business card - Helicopter Flight Services, Flight School, etc.

We need a business card design for a new helicopter service.

We offer Helicopter Flight Services, Aerial Filming & Photography, Flight School, and Helicopter Tours. In that order.

Summit BladeAir, Inc.
Dennis Tollerby
SummitBladeair@Kestmail.com
626-418-7352

Based at the Brenwick Airport in Van Nuys, CA. The final design should communicate integrity and safety. Pictures or logos at your discretion.

Card back side - surprise me.

```html
<!DOCTYPE html>
<html lang="en">
<head>
<meta charset="utf-8">
<title>Summit BladeAir, Inc. — Business Card</title>
<link href="https://fonts.googleapis.com/css2?family=Bodoni+Moda:wght@600;700&family=Roboto:wght@300;400&display=swap" rel="stylesheet">
<style>
  :root {
    --page: #e9e7e3;
    --card-black: #07070c;
    --frame-white: #f2f2f2;
    --band-grey: #262827;
    --text-light: #e6e6e6;
    --text-soft: #c9c9c9;
    --rule: #bdbdbd;
    --sky-top: #b9c6da;
    --sky-mid: #d9e2ec;
    --sky-low: #e6d4dc;
    --icon-gold: #c8a96a;
  }
  * { box-sizing: border-box; margin: 0; padding: 0; }
  html, body { width: 1200px; height: 902px; overflow: hidden; }
  body {
    background: var(--page);
    display: flex;
    flex-direction: column;
    align-items: center;
    justify-content: center;
    gap: 42px;
  }
  .card {
    position: relative;
    width: 700px;
    height: 400px;
    background: var(--card-black);
    box-shadow: 0 6px 18px rgba(0,0,0,.25);
  }
  .card__frame {
    position: absolute;
    inset: 38px 42px;
    border: 7px solid var(--frame-white);
    overflow: hidden;
  }

  /* Back side: photo panel */
  .photo {
    position: absolute;
    inset: 0;
    background: linear-gradient(180deg, var(--sky-top) 0%, var(--sky-mid) 55%, var(--sky-low) 100%);
  }
  .back__text {
    position: absolute;
    left: 0; right: 0;
    top: 150px;
    text-align: center;
    font-family: "Bodoni Moda", serif;
    color: #141418;
  }
  .back__company {
    font-size: 30px;
    font-weight: 700;
    letter-spacing: 2px;
    text-transform: uppercase;
  }
  .back__services {
    margin-top: 6px;
    font-size: 21px;
    font-weight: 700;
    letter-spacing: 1px;
  }

  /* Front side: contact card */
  .front__frame { background: var(--card-black); }
  .front__band {
    position: absolute;
    left: 0; right: 0; bottom: 0;
    height: 52%;
    background: var(--band-grey);
  }
  .front__company {
    position: absolute;
    top: 52px; left: 0; right: 0;
    text-align: center;
    font-family: "Bodoni Moda", serif;
    font-weight: 700;
    font-size: 31px;
    letter-spacing: 2px;
    color: var(--text-light);
    text-transform: uppercase;
  }
  .front__name {
    position: absolute;
    left: 40px;
    top: 158px;
    font-family: "Bodoni Moda", serif;
    font-weight: 700;
    font-size: 23px;
    color: var(--text-light);
  }
  .contact {
    position: absolute;
    left: 300px;
    top: 128px;
    font-family: "Roboto", sans-serif;
    font-weight: 300;
    font-size: 14px;
    color: var(--text-soft);
  }
  .contact__row { display: flex; align-items: center; gap: 10px; height: 30px; }
  .contact__rule {
    width: 220px;
    height: 1px;
    background: var(--rule);
    margin-top: 4px;
  }
  .address {
    position: absolute;
    left: 0; right: 0;
    top: 218px;
    text-align: center;
    font-family: "Roboto", sans-serif;
    font-weight: 300;
    font-size: 15px;
    line-height: 1.35;
    color: var(--text-soft);
  }
  .address__marker {
    display: flex;
    align-items: center;
    justify-content: center;
    gap: 10px;
    margin-bottom: 10px;
  }
  .address__line { width: 130px; height: 1px; background: var(--rule); }
</style>
</head>
<body>

  <section class="card card--back" aria-label="Card back">
    <div class="card__frame">
      <div class="photo" role="img" aria-label="Photo of a helicopter flying against a pale sky, dropping flower petals"></div>
      <div class="back__text">
        <p class="back__company">Summit BladeAir, Inc.</p>
        <p class="back__services">Airport · Tour guide · Heliport</p>
      </div>
    </div>
  </section>

  <section class="card card--front" aria-label="Card front">
    <div class="card__frame front__frame">
      <div class="front__band"></div>
      <h1 class="front__company">Summit BladeAir, Inc.</h1>
      <p class="front__name">Dennis Tollerby</p>
      <div class="contact">
        <div class="contact__row">
          <svg width="18" height="18" viewBox="0 0 24 24" aria-hidden="true">
            <circle cx="12" cy="12" r="10.5" fill="none" stroke="#e6e6e6" stroke-width="1.5"/>
            <path d="M9 7.5c.6-.4 1.2-.2 1.5.4l.8 1.6c.2.5.1 1-.3 1.3l-.6.5c.5 1.2 1.3 2 2.4 2.5l.5-.6c.3-.4.9-.5 1.3-.3l1.6.8c.6.3.8.9.4 1.5-.6 1-1.8 1.4-2.8 1-2.6-1-4.5-2.9-5.4-5.5-.3-1 .1-2.2.6-2.7z" fill="#e6e6e6"/>
          </svg>
          <span>626-418-7352</span>
        </div>
        <div class="contact__row">
          <svg width="18" height="18" viewBox="0 0 24 24" aria-hidden="true">
            <circle cx="12" cy="12" r="11" fill="var(--icon-gold)"/>
            <rect x="6" y="8" width="12" height="8" fill="#fff"/>
            <path d="M6 8l6 4.5L18 8" fill="none" stroke="var(--icon-gold)" stroke-width="1.2"/>
          </svg>
          <span>SummitBladeair@Kestmail.com</span>
        </div>
        <div class="contact__rule"></div>
      </div>
      <div class="address">
        <div class="address__marker">
          <span class="address__line"></span>
          <svg width="26" height="26" viewBox="0 0 24 24" aria-hidden="true">
            <circle cx="12" cy="12" r="11" fill="none" stroke="#e6e6e6" stroke-width="1.2"/>
            <path d="M12 5.5a4 4 0 0 0-4 4c0 3 4 8 4 8s4-5 4-8a4 4 0 0 0-4-4z" fill="none" stroke="#e6e6e6" stroke-width="1.4"/>
            <circle cx="12" cy="9.5" r="1.4" fill="#e6e6e6"/>
          </svg>
          <span class="address__line"></span>
        </div>
        <p>2870 W. Larkfield Ave. Ste.B</p>
        <p>Van Nuys, CA 91405</p>
      </div>
    </div>
  </section>

</body>
</html>
```